Corvell Keystone Lighting Commercial & Residential Landscape Lighting

Hello, I am looking for an Ad Design that I can use to promote ads on Plumora and other social media platforms. I want this ad to be a split screen ad meaning one photo at the top and one photo at the bottom to include a southern style home without outdoor landscape lighting & then the same picture at the bottom with outdoor landscape lighting. Add text to the graphic that talks about the difference landscape lighting does to your home. I want this ad to look professional and have professional design elements to the ad. I also have a logo I have uploaded below. We specialize in commercial grade outdoor landscape lighting, custom flag poles, outdoor audio, and we are locally and veteran owned. We offer lifetime warranty and quarterly maintenance on products.

```html
<!DOCTYPE html>
<html lang="en">
<head>
<meta charset="utf-8">
<title>Corvell Keystone Lighting – Social Ad</title>
<link rel="stylesheet" href="https://fonts.googleapis.com/css2?family=Poppins:wght@400;600;700;800&family=Oswald:wght@400;500&display=swap">
<style>
  :root {
    --page: #ffffff;
    --ink: #050505;
    --gold: #e2a41f;
    --logo-orange: #f0a030;
    --cream: #f8dcb8;
    --white: #ffffff;
    --dot: #3a3a3a;
  }
  html, body {
    margin: 0;
    padding: 0;
    width: 1200px;
    height: 586px;
    overflow: hidden;
    background: var(--page);
  }
  .canvas {
    position: relative;
    width: 1200px;
    height: 586px;
    display: flex;
    align-items: center;
    justify-content: center;
  }
  .ad {
    width: 540px;
    height: 540px;
    display: block;
  }
  .brand-name { font-family: "Poppins", sans-serif; font-weight: 400; fill: var(--logo-orange); }
  .headline-light { font-family: "Poppins", sans-serif; font-weight: 400; fill: var(--white); }
  .headline-gold { font-family: "Poppins", sans-serif; fill: var(--gold); }
  .band-text { font-family: "Poppins", sans-serif; font-weight: 400; fill: var(--ink); }
  .contact { font-family: "Oswald", sans-serif; font-weight: 400; fill: var(--white); }
</style>
</head>
<body>
<main class="canvas">
  <svg class="ad" viewBox="0 0 1050 1050" xmlns="http://www.w3.org/2000/svg" aria-label="Corvell Keystone Lighting landscape lighting ad">
    <defs>
      <linearGradient id="stripe-light" x1="0" y1="0" x2="0" y2="1">
        <stop offset="0" stop-color="#f6dfc0"/>
        <stop offset="0.55" stop-color="#8a7458"/>
        <stop offset="1" stop-color="#050505" stop-opacity="0"/>
      </linearGradient>
      <linearGradient id="stripe-gold" x1="0" y1="0" x2="0" y2="1">
        <stop offset="0" stop-color="#e2a41f"/>
        <stop offset="1" stop-color="#6b4d10"/>
      </linearGradient>
      <linearGradient id="stripe-gold-low" x1="0" y1="0" x2="0" y2="1">
        <stop offset="0" stop-color="#e2a41f"/>
        <stop offset="1" stop-color="#050505" stop-opacity="0"/>
      </linearGradient>
      <linearGradient id="photo-dusk" x1="0" y1="0" x2="0" y2="1">
        <stop offset="0" stop-color="#2f62b0"/>
        <stop offset="0.35" stop-color="#3a5a7a"/>
        <stop offset="0.5" stop-color="#7a4a28"/>
        <stop offset="0.65" stop-color="#3f6a2a"/>
        <stop offset="1" stop-color="#2b5a1e"/>
      </linearGradient>
      <linearGradient id="photo-lit" x1="0" y1="0" x2="0" y2="1">
        <stop offset="0" stop-color="#24477e"/>
        <stop offset="0.3" stop-color="#2d4530"/>
        <stop offset="0.5" stop-color="#b0702a"/>
        <stop offset="0.68" stop-color="#3c6a22"/>
        <stop offset="1" stop-color="#2a5a18"/>
      </linearGradient>
    </defs>

    <!-- base -->
    <rect class="ad-background" x="0" y="0" width="1050" height="1050" fill="var(--ink)"/>

    <!-- upper photo: home at dusk -->
    <path class="photo-upper" role="img" aria-label="Photo of a large southern-style home at dusk on a wide green lawn"
          d="M655 178 H1050 V636 H365 V600 L520 420 Z" fill="url(#photo-dusk)"/>

    <!-- lower photo: home with landscape lighting -->
    <path class="photo-lower" role="img" aria-label="Photo of the same home at night lit by warm outdoor landscape lighting"
          d="M0 596 H340 V661 H690 L430 1050 H0 Z" fill="url(#photo-lit)"/>

    <!-- accent stripes -->
    <polygon class="accent-stripe" points="690,0 760,0 575,290 505,290" fill="url(#stripe-light)"/>
    <polygon class="accent-stripe" points="780,0 830,0 715,172 665,172" fill="url(#stripe-gold)"/>
    <polygon class="accent-stripe" points="722,636 770,636 630,850 582,850" fill="url(#stripe-gold-low)"/>

    <!-- dot grid -->
    <g class="dot-grid" fill="var(--dot)">
      <circle cx="860" cy="76" r="4"/><circle cx="883" cy="76" r="4"/><circle cx="906" cy="76" r="4"/><circle cx="929" cy="76" r="4"/><circle cx="952" cy="76" r="4"/><circle cx="975" cy="76" r="4"/><circle cx="998" cy="76" r="4"/>
      <circle cx="860" cy="93" r="4"/><circle cx="883" cy="93" r="4"/><circle cx="906" cy="93" r="4"/><circle cx="929" cy="93" r="4"/><circle cx="952" cy="93" r="4"/><circle cx="975" cy="93" r="4"/><circle cx="998" cy="93" r="4"/>
      <circle cx="860" cy="110" r="4"/><circle cx="883" cy="110" r="4"/><circle cx="906" cy="110" r="4"/><circle cx="929" cy="110" r="4"/><circle cx="952" cy="110" r="4"/><circle cx="975" cy="110" r="4"/><circle cx="998" cy="110" r="4"/>
    </g>

    <!-- brand name -->
    <g class="brand">
      <text class="brand-name" x="46" y="192" font-size="96" letter-spacing="2">CORVELL</text>
      <text class="brand-name" x="48" y="222" font-size="25" letter-spacing="5">KEYSTONE LIGHTING</text>
    </g>

    <!-- headline -->
    <g class="headline">
      <text class="headline-light" x="48" y="348" font-size="52">When the Sun</text>
      <text class="headline-light" x="48" y="394" font-size="52">Goes Down,</text>
      <text class="headline-gold" x="48" y="480" font-size="86">
        <tspan font-weight="400">Your </tspan><tspan font-weight="700">Home</tspan>
      </text>
      <rect class="headline-band" x="0" y="496" width="362" height="68" fill="var(--cream)"/>
      <text class="band-text" x="50" y="549" font-size="50">Should Still</text>
      <text class="headline-gold" x="378" y="566" font-size="96" font-weight="700">Shine</text>
    </g>

    <!-- contact -->
    <g class="contact-block">
      <text class="contact" x="955" y="958" font-size="36" text-anchor="end">(555)204-7318</text>
      <text class="contact" x="955" y="996" font-size="30" text-anchor="end">info@corvellkeystone.com</text>
      <g class="icon-mail" transform="translate(970,932)">
        <rect x="0" y="0" width="32" height="22" fill="var(--gold)"/>
        <polyline points="0,0 16,12 32,0" fill="none" stroke="var(--ink)" stroke-width="2.5"/>
      </g>
      <path class="icon-phone" transform="translate(972,970)" fill="var(--gold)"
            d="M6 0 L13 0 L16 9 L11 13 C13 18 17 22 22 24 L26 19 L34 22 L34 29 C34 31 32 33 29 33 C13 32 2 20 1 5 C1 2 3 0 6 0 Z"/>
    </g>
  </svg>
</main>
</body>
</html>
```